Occasions chocolate packaging

We are looking for 7 packaging designs for bars of chocolate.

Each design needs to be different and we’re not looking for a consistent brand or branding message across the designs. Inspiration should come from gift/occasion cards. Fun, simple, bold, vibrant colours and eye catching, i.e. not vintage or just text.

The front of the packaging should have the main message on and is free of any branding. You don’t need to design the back, just simply allow the main background colour or design pattern to continue around.

These are the different designs we are after, I’ve added in some text for each to give you some guidance but feel free to play around with the message if it suits the design better.

1) Mum
‘The best mum’, ‘Best mum in the World’, ‘Number 1 Mum’

2) Dad
‘The Best Dad’, ‘Best Dad Ever’, ‘Number 1 Dad’, ‘You’re my hero Dad’

3) Husband
‘Best Husband in the World’, ‘Husband I Love You’, ‘Darling Husband’

4) Wife
‘Best Wife in the World’, ‘For my Wonderful Wife’, ‘My Beautiful Wife’

5) Congratulations
Simple one, just Congratulations

6) Thinking of you
Try and keep this neutral as it could be used for happy and sad situations.

7) Thank you
Keep this gender neutral.

Sides:
The sides need to have the following text:

FINE BELGIAN DARK CHOCOLATE
infused with Orange

Back:
The main colour of the front should continue all the way around, we will place a box with the contents and bar code on here ourselves so no need to do anything.

Dimensions:
Attached in the document, front of package is 85mm by 190mm.

The packaging is made from folded card, the first blank part is for gluing the back on to.

Reason: I'm extending the deadline as I've only received 1 design so far which has followed the brief. Although I do like it, I would like to see at least some competition...

```html
<!DOCTYPE html>
<html lang="en">
<head>
<meta charset="utf-8">
<title>Best Hubby in the World – Chocolate Bar Wrap</title>
<link rel="stylesheet" href="https://fonts.googleapis.com/css2?family=Oswald:wght@500;700&family=Montserrat:ital,wght@0,600;1,500;1,700&display=swap">
<style>
  :root {
    --stage: #e9eaec;
    --orange: #c9640f;
    --orange-light: #d8721a;
    --orange-side: #a44c0a;
    --heart-pink: #e8178f;
    --white: #ffffff;
  }
  * { margin: 0; padding: 0; box-sizing: border-box; }
  html, body {
    width: 1200px; height: 960px; overflow: hidden;
    background: var(--stage);
  }
  .wrap {
    position: absolute; left: 389px; top: 70px;
    width: 422px; height: 820px;
    display: flex;
  }
  .side-panel {
    position: relative;
    width: 52px; height: 100%;
    background: var(--orange-side);
    overflow: hidden;
  }
  .side-text {
    position: absolute; left: 50%; top: 50%;
    transform: translate(-50%, -50%) rotate(-90deg);
    white-space: nowrap;
    color: var(--white);
    font-family: "Montserrat", sans-serif;
    letter-spacing: 2px;
  }
  .side-title { font-weight: 700; font-style: italic; font-size: 19px; }
  .side-flavour { font-weight: 500; font-style: italic; font-size: 16px; margin-left: 22px; }
  .front-panel {
    position: relative;
    width: 370px; height: 100%;
    background: radial-gradient(ellipse at 50% 55%, var(--orange-light), var(--orange) 70%);
    overflow: hidden;
  }
  .couple-heart-illustration {
    position: absolute; left: 40px; top: 30px;
    width: 290px; height: 480px;
    border-radius: 120px 120px 12px 12px;
    background: linear-gradient(180deg, var(--heart-pink) 0%, #f07ab9 40%, rgba(255,255,255,0.85) 75%, rgba(255,255,255,0.7) 100%);
  }
  .message {
    position: absolute; left: 0; right: 0; top: 535px;
    text-align: center;
    color: var(--white);
    font-family: "Oswald", sans-serif;
    font-weight: 700;
    line-height: 0.95;
  }
  .word-best { font-size: 112px; letter-spacing: -1px; }
  .word-hubby { font-size: 76px; }
  .word-world { font-size: 40px; font-weight: 500; letter-spacing: -1px; margin-top: 8px; }
  .line-love {
    font-family: "Montserrat", sans-serif;
    font-weight: 600; font-size: 22px;
    letter-spacing: 3px; margin-top: 14px;
  }
</style>
</head>
<body>
  <div class="wrap">
    <div class="side-panel">
      <div class="side-text">
        <span class="side-title">FINE BELGIAN DARK CHOCOLATE</span><span class="side-flavour">infused with Orange</span>
      </div>
    </div>
    <div class="front-panel">
      <div class="couple-heart-illustration" role="img" aria-label="Large pink heart behind a white silhouette of an embracing couple, with small white sparkles scattered over the striped orange background"></div>
      <div class="message">
        <div class="word-best">BEST</div>
        <div class="word-hubby">HUBBY</div>
        <div class="word-world">IN THE WORLD</div>
        <div class="line-love">HUSBAND I LOVE YOU</div>
      </div>
    </div>
  </div>
</body>
</html>
```